Business Card Design

We like to use greens as you will see in our logo (but not TOO much green). We are a Dental Clinic in a somewhat eccentric community. We do not like the dated sharp designs which we see many dentists use. We're looking for something bright and fresh while still maintaining the integrity of the profession. Elegance is not necessarily what we are going for... we need for the design to be "mature" but also up-lifting.

See our logo.
Updates

Project Deadline Extended
Reason: We have 5 designs which we like. But we'd like to see a few more before committing to a design.

Project Deadline Extended
Reason: We are awaiting revisions to this project. We are still welcoming designs while we wait to see if designers are able to provide to us the revisions we require in order to proceed with a selection.

Target Market(s)

Younger families - ages late 20's to early 40's

Industry/Entity Type

Business

Contact Information for Business Card

Corwel T. Banfry DDS 2730 W. Halvert Rd. Ste. 7 Royal Oak, MI 48391 (248)555-0174 FX (248)555-0189 info@BrightwellDentalCareMi.com BrigthwellDentalCareMi.com on the back of the card we need an appointment reminder (For____ Date___ Time____) with "If you are unable to keep your appointment, kindly give 48 hours notice" at the bottom. No use of teeth in the design. DOUBLE SIDED DESIGN

Requirements
Should not have
• The use of pictures of teeth

```html
<!DOCTYPE html>
<html lang="en">
<head>
<meta charset="utf-8">
<title>Brightwell Dental Care – Business Card</title>
<link rel="stylesheet" href="https://fonts.googleapis.com/css2?family=Arimo:wght@400;700&family=Open+Sans:ital,wght@0,400;0,600;0,700;1,400&family=Cinzel:wght@600&display=swap">
<style>
  :root {
    --green-dark: #1a6b3a;
    --green-mid: #237a41;
    --green-light: #3aa64c;
    --ink: #222222;
    --ink-soft: #333333;
    --paper: #ffffff;
    --stage: #ecece8;
    --rule: #c9c9c9;
  }
  * { box-sizing: border-box; margin: 0; padding: 0; }
  html, body { width: 1200px; height: 1160px; overflow: hidden; }
  body { background: var(--stage); position: relative; font-family: "Arimo", Arial, sans-serif; color: var(--ink); }

  .card {
    position: absolute;
    width: 910px; height: 518px;
    background: var(--paper);
    border-radius: 38px;
    overflow: hidden;
    box-shadow: 0 4px 14px rgba(0,0,0,.18);
  }
  .card--front { left: 29px; top: 35px; }
  .card--back { left: 254px; top: 593px; border: 2px solid #d5d5d5; }

  .brand-name {
    position: absolute;
    font-family: "Open Sans", sans-serif;
    font-weight: 600;
    color: var(--green-dark);
    line-height: 1.05;
  }
  .brand-name .dot {
    display: inline-block; width: 0.5em; height: 0.5em; border-radius: 50%;
    background: var(--green-light); margin-right: 0.25em; vertical-align: 0.15em;
  }
  .card--front .brand-name { left: 64px; top: 92px; font-size: 50px; }
  .card--front .brand-name small { display: block; font-size: 40px; letter-spacing: 1px; }

  .front-rule {
    position: absolute; left: 0; top: 262px; width: 100%; height: 3px;
    background: linear-gradient(90deg, rgba(200,200,200,0), var(--rule) 15%, var(--rule) 85%, rgba(200,200,200,0));
  }

  .doctor { position: absolute; left: 66px; top: 280px; }
  .doctor__name { font-size: 36px; font-weight: 700; color: var(--ink); }
  .doctor__title { font-size: 22px; font-weight: 700; margin-top: 12px; }
  .address { position: absolute; left: 66px; top: 386px; font-size: 24px; line-height: 33px; color: var(--ink-soft); }

  .contacts { position: absolute; right: 30px; top: 290px; list-style: none; text-align: right; font-size: 24px; color: var(--ink-soft); }
  .contacts li { height: 42px; display: flex; justify-content: flex-end; align-items: center; gap: 10px; }
  .contacts svg { width: 22px; height: 22px; fill: var(--ink-soft); }
  .contacts li:nth-child(4) { font-size: 22px; }

  .front-band { position: absolute; left: 0; bottom: 0; width: 100%; height: 62px; }

  /* back */
  .card--back .brand-name { right: 50px; top: 62px; font-size: 40px; text-align: left; }
  .card--back .brand-name small { display: block; font-size: 31px; letter-spacing: 1px; }
  .appt-title {
    position: absolute; left: 70px; top: 100px;
    font-family: "Cinzel", serif; font-weight: 600; font-size: 35px; color: var(--green-dark); letter-spacing: 1px;
  }
  .appt-form { font-family: "Open Sans", sans-serif; font-size: 24px; color: var(--ink-soft); }
  .field { position: absolute; left: 80px; display: flex; align-items: baseline; }
  .field__line { border-bottom: 2px dotted #666; height: 1px; margin: 0 8px; }
  .field--name { top: 178px; }
  .field--name .field__line { width: 665px; margin-left: 16px; }
  .field--date { top: 240px; }
  .field--date .field__line.is-date { width: 230px; margin-left: 28px; }
  .field--date .field__line.is-time { width: 250px; }
  .field--next { top: 302px; align-items: center; }
  .next-box { width: 163px; height: 36px; border: 2px solid #555; border-radius: 4px; margin-left: 12px; }
  .next-box:first-of-type { margin-left: 18px; }

  .day-band {
    position: absolute; left: 0; top: 358px; width: 100%; height: 79px;
    display: flex; background: var(--green-mid);
    font-family: "Open Sans", sans-serif; font-weight: 700; font-size: 24px; color: #fff;
  }
  .day-band__week {
    width: 719px; flex: none; display: flex; align-items: center;
    padding-left: 80px; gap: 24px; position: relative; z-index: 1;
  }
  .day-band__sat {
    flex: 1; background: var(--green-light); display: flex; align-items: center;
    padding-left: 30px; border-left: 4px solid #fff;
  }
  .day { display: flex; align-items: center; gap: 10px; white-space: nowrap; }
  .day__box { width: 54px; height: 33px; background: #fff; border-radius: 4px; border: 2px solid var(--green-dark); }

  .notice {
    position: absolute; left: 0; width: 100%; top: 458px; text-align: center;
    font-family: "Open Sans", sans-serif; font-style: italic; font-size: 24px; color: var(--ink);
  }
</style>
</head>
<body>

<section class="card card--front" aria-label="Business card front">
  <div class="brand-name"><span class="dot"></span>Brightwell<small>DENTAL CARE</small></div>
  <div class="front-rule"></div>

  <div class="doctor">
    <p class="doctor__name">Corwel T. Banfry</p>
    <p class="doctor__title">DDS</p>
  </div>
  <p class="address">2730 W. Halvert Rd.<br>Ste. 7 Royal Oak, MI 48391</p>

  <ul class="contacts">
    <li><svg viewBox="0 0 24 24" aria-hidden="true"><path d="M6.6 10.8a15 15 0 0 0 6.6 6.6l2.2-2.2c.3-.3.7-.4 1-.2 1.1.4 2.3.6 3.6.6.6 0 1 .4 1 1V20c0 .6-.4 1-1 1A17 17 0 0 1 3 4c0-.6.4-1 1-1h3.5c.6 0 1 .4 1 1 0 1.3.2 2.5.6 3.6.1.3 0 .7-.2 1z"/></svg>(248) 555-0174</li>
    <li><svg viewBox="0 0 24 24" aria-hidden="true"><path d="M6 3h10v5H6zM3 9h18v9h-3v3H6v-3H3zm5 7v3h8v-3z"/></svg>(248) 555-0189</li>
    <li><svg viewBox="0 0 24 24" aria-hidden="true"><path d="M2 6h20v13H2zm2 2v.5l8 5 8-5V8l-8 5z"/></svg>info@BrightwellDentalCareMi.com</li>
    <li><svg viewBox="0 0 24 24" aria-hidden="true"><path d="M12 2a10 10 0 1 0 0 20 10 10 0 0 0 0-20zm0 2c.9 1.2 1.6 2.6 2 4h-4c.4-1.4 1.1-2.8 2-4zM4.3 14a8 8 0 0 1 0-4h3.4a16 16 0 0 0 0 4zm.9 2h3c.3 1.3.8 2.5 1.4 3.6A8 8 0 0 1 5.2 16zm3-8h-3a8 8 0 0 1 4.4-3.6C8 5.5 7.5 6.7 8.2 8zM12 20c-.9-1.2-1.6-2.6-2-4h4c-.4 1.4-1.1 2.8-2 4zm2.3-6H9.7a14 14 0 0 1 0-4h4.6a14 14 0 0 1 0 4zm.1 5.6c.6-1.1 1.1-2.3 1.4-3.6h3a8 8 0 0 1-4.4 3.6zM16.3 14a16 16 0 0 0 0-4h3.4a8 8 0 0 1 0 4zm-.5-6c-.3-1.3-.8-2.5-1.4-3.6A8 8 0 0 1 18.8 8z"/></svg>BrigthwellDentalCareMi.com</li>
  </ul>

  <svg class="front-band" viewBox="0 0 910 62" preserveAspectRatio="none" aria-hidden="true">
    <polygon fill="#1a6b3a" points="0,62 0,18 13,4 26,18 39,4 52,18 65,4 78,18 91,4 104,18 117,4 130,18 143,4 156,18 169,4 182,18 195,4 208,18 221,4 234,18 247,4 260,18 273,4 286,18 299,4 312,18 325,4 338,18 351,4 364,18 377,4 390,18 403,4 416,18 429,4 442,18 455,4 468,18 481,4 494,18 507,4 520,18 533,4 546,18 559,4 572,18 585,4 598,18 611,4 624,18 637,4 650,18 663,4 676,18 689,4 702,18 715,4 728,18 741,4 754,18 767,4 780,18 793,4 806,18 819,4 832,18 845,4 858,18 871,4 884,18 897,4 910,18 910,62"/>
  </svg>
</section>

<section class="card card--back" aria-label="Business card back">
  <h2 class="appt-title">YOUR APPOINTMENT</h2>
  <div class="brand-name"><span class="dot"></span>Brightwell<small>DENTAL CARE</small></div>

  <div class="appt-form">
    <div class="field field--name">Name :<span class="field__line"></span></div>
    <div class="field field--date">Date :<span class="field__line is-date"></span>Time :<span class="field__line is-time"></span>am / pm</div>
    <div class="field field--next">Next Appointment<span class="next-box"></span><span class="next-box"></span><span class="next-box"></span></div>
  </div>

  <div class="day-band">
    <div class="day-band__week">
      <span class="day">MON<span class="day__box"></span></span>
      <span class="day">TUE<span class="day__box"></span></span>
      <span class="day">WED<span class="day__box"></span></span>
      <span class="day">THU<span class="day__box"></span></span>
      <span class="day">FRI<span class="day__box"></span></span>
    </div>
    <div class="day-band__sat"><span class="day">SAT<span class="day__box"></span></span></div>
  </div>

  <p class="notice">If you are unable to keep your appointment, kindly give 48 hours notice</p>
</section>

</body>
</html>
```